Building company buisness cards

We are looking for a sharp modern new look for our business cards.We are a New Zealand based company that specialises in house and land packages.We have attached a photo of the current logo and would like to see if it can be improved somehow if needed.We are open to any colours but we have chosen Black and White at this stage. Feel free to change the font and make the logo smarter looking.Play with the colours and see what looks best.We want a card that looks so good know one will want to throw it away!

Target Market(s)

Building profesonals, home buyers

Industry/Entity Type

Building

Contact Information for Business Card

Garrick Tenwood
0275390628
garrickt@hartvale.co.nz

Font styles to use
Serif
Sans Serif

Colors

Designer to choose colors to be used in the design.

Requirements
Must have
• Just the logo on one side and details on the other
• Clean simple looking card
Nice to have
• Round corners and detail like raised or spot UV
• Something that stands out
Should not have
• To title needed, Director etc

```html
<!DOCTYPE html>
<html lang="en">
<head>
<meta charset="utf-8">
<title>Hartvale Business Cards</title>
<link rel="stylesheet" href="https://fonts.googleapis.com/css2?family=Playfair+Display:wght@900&family=Montserrat:wght@300;400&display=swap">
<style>
  :root {
    --ink: #0b0b0b;
    --paper: #ffffff;
    --backdrop: #d6d6d6;
    --serif: "Playfair Display", Georgia, serif;
    --sans: "Montserrat", Arial, sans-serif;
  }
  * { margin: 0; padding: 0; box-sizing: border-box; }
  html, body { width: 1200px; height: 900px; overflow: hidden; }
  body { background: var(--backdrop); position: relative; font-family: var(--sans); }

  .card {
    position: absolute;
    width: 560px;
    height: 320px;
    border-radius: 22px;
    overflow: hidden;
  }
  .card--front { left: 320px; top: 100px; background: var(--ink); color: var(--paper); }
  .card--back  { left: 320px; top: 480px; background: var(--paper); color: var(--ink); }

  .front-lockup {
    position: absolute;
    left: 0; right: 0;
    top: 96px;
    text-align: center;
  }
  .brand-name {
    font-family: var(--serif);
    font-weight: 900;
    line-height: 1;
    letter-spacing: -1px;
  }
  .front-lockup .brand-name { display: block; font-size: 80px; color: var(--paper); }
  .tagline {
    font-family: var(--sans);
    font-weight: 300;
    font-size: 17px;
    letter-spacing: 1.5px;
    margin-top: 8px;
  }

  .back-name { position: absolute; right: 46px; top: 44px; font-size: 70px; color: var(--ink); }

  .contact-band {
    position: absolute;
    left: 150px; right: 0;
    top: 150px; height: 104px;
    background: var(--ink);
    color: var(--paper);
    padding: 12px 0 0 80px;
  }
  .contact-band__name {
    font-family: var(--serif);
    font-weight: 900;
    font-size: 23px;
    letter-spacing: 0.5px;
    margin-bottom: 8px;
  }
  .contact-line {
    display: flex; align-items: center; gap: 8px;
    font-size: 15px; font-weight: 400;
    line-height: 1.4;
  }
  .contact-line svg { width: 14px; height: 14px; fill: var(--paper); flex: none; }
</style>
</head>
<body>
  <section class="card card--front" aria-label="Card front">
    <div class="front-lockup">
      <span class="brand-name">Hartvale</span>
      <p class="tagline">Built around your life.</p>
    </div>
  </section>

  <section class="card card--back" aria-label="Card back">
    <span class="brand-name back-name">Hartvale</span>
    <div class="contact-band">
      <p class="contact-band__name">Garrick Tenwood</p>
      <p class="contact-line">
        <svg viewBox="0 0 24 24" aria-hidden="true"><path d="M6.6 10.8a15.1 15.1 0 0 0 6.6 6.6l2.2-2.2a1 1 0 0 1 1-.25 11.4 11.4 0 0 0 3.6.57 1 1 0 0 1 1 1V20a1 1 0 0 1-1 1A17 17 0 0 1 3 4a1 1 0 0 1 1-1h3.5a1 1 0 0 1 1 1c0 1.250.2 2.45.57 3.57a1 1 0 0 1-.25 1z"/></svg>
        <span>0275390628</span>
      </p>
      <p class="contact-line">
        <svg viewBox="0 0 24 24" aria-hidden="true"><path d="M2 5h20v14H2z M4 7v.4l8 5.2 8-5.2V7z" fill-rule="evenodd"/></svg>
        <span>garrickt@hartvale.co.nz</span>
      </p>
    </div>
  </section>
</body>
</html>
```